CREATE A KILLER WEBSITE DESIGN

We are a firearms training company that trains CIVILIANS (no police or military pictures - thank you!) to defend themselves and are looking for a killer design that's clean, easy to navigate and modern! We want the newest trends applied to this sight like a scrollable site so you can scroll down and see all the features. We are okay with tweaking the HTML but need the artistic design to look good. I'll provide a link to our current site along with a sight we really like so you can get an idea!

I'm supplying a PowerPoint Design we are going with from another designer so you can match the style to the new site.

PAGES: (Please use information from our current site. We like the information but just want a more polished look similar to the NWDPA site below but in our colors.)
Home - Long Form Scrolling Site. Top fold will be a video with a play button.
Harbor Institute - Seven Level Training Program Info Page That Will Contain A Video.
Contact Us - This will be a page that DOES NOT CONTAIN AN EMAIL ADDRESS. Just a contact us form
Meet The Trainer: Dennis Pollock

Our site:
https://www.brightmeadowskills.biz

Sights We Like:
https://www.nwdefenseplanners.com
https://quorvel.com
https://lindenplatecorp.com
https://www.velbrookgear.com

Target Market(s)

Men and women ages 21 to 100 years old

Industry/Entity Type

Self Defense

Number of Pages Required

5+ page

Font styles to use
Sans Serif

Colors
f26267

Requirements
Must have
• Clean and engaging. Use of colors that match our logo.
Should not have
• Poor design quality

```html
<!DOCTYPE html>
<html lang="en">
<head>
<meta charset="utf-8">
<title>Bright Meadow Skills — Home</title>
<link href="https://fonts.googleapis.com/css2?family=Montserrat:wght@400;500;600;700;800&display=swap" rel="stylesheet">
<style>
:root{
  --coral:#f26267;
  --ink:#232323;
  --dark:#2a2a2a;
  --charcoal:#3c3c3c;
  --paper:#f4f4f4;
  --white:#ffffff;
  --grey:#5a5a5a;
}
*{margin:0;padding:0;box-sizing:border-box}
html,body{width:1200px;height:4192px;overflow:hidden}
body{position:relative;background:var(--paper);font-family:"Montserrat",sans-serif;color:var(--ink)}
.abs{position:absolute}
.center{text-align:center}

/* header */
.site-header{position:absolute;left:0;top:0;width:1200px;height:100px;background:var(--dark);color:var(--white)}
.brand{position:absolute;left:94px;top:24px;width:110px;display:flex;flex-direction:column;align-items:center;gap:6px}
.brand-dot{width:22px;height:22px;border-radius:50%;background:var(--coral)}
.brand-name{font-size:11px;font-weight:800;letter-spacing:1px;color:var(--white)}
.tagline{position:absolute;left:220px;top:26px;font-size:14px;font-weight:800;letter-spacing:1.5px}
.utility{position:absolute;right:92px;top:27px;display:flex;gap:30px;font-size:11px;font-weight:600}
.utility .login{color:var(--coral)}
.main-nav{position:absolute;left:220px;top:66px;display:flex;gap:38px;font-size:12.5px;font-weight:600;letter-spacing:.5px}
.main-nav .active{position:relative}
.main-nav .active::before{content:"";position:absolute;left:8px;top:-6px;width:24px;height:24px;border-radius:50%;background:var(--coral);opacity:.35;z-index:-1}
.nav-cta{position:absolute;left:894px;top:57px;width:212px;height:32px;background:var(--coral);color:var(--white);font-size:12.5px;font-weight:700;letter-spacing:.5px;display:flex;align-items:center;justify-content:center}

/* hero */
.hero{position:absolute;left:0;top:100px;width:1200px;height:590px;overflow:hidden}
.hero-media{position:absolute;inset:0;background:radial-gradient(ellipse at 88% 50%,#f2f0e6 0%,#b9c8bd 14%,#5c7c76 34%,#2c4d4d 62%,#1d3536 100%)}
.hero h1{position:absolute;left:0;top:176px;width:1200px;text-align:center;color:var(--white);font-size:46px;font-weight:800;line-height:50px}
.hero .lead{position:absolute;left:0;top:280px;width:1200px;text-align:center;color:#e0e0e0;font-size:16px}
.btn{display:flex;align-items:center;justify-content:center;font-weight:700;font-size:12.5px;letter-spacing:.5px;color:var(--white)}
.btn-solid{background:var(--coral)}
.btn-outline{border:2px solid var(--coral)}
.hero-divider{position:absolute;left:671px;top:336px;width:1px;height:134px;background:rgba(255,255,255,.6)}
.play-film{position:absolute;left:700px;top:348px;width:114px;text-align:center;color:var(--white);font-size:14px;font-weight:700}

/* about */
.about{position:absolute;left:0;top:690px;width:1200px;height:640px;background:var(--dark)}
.portrait{position:absolute;left:94px;top:0;width:505px;height:640px;background:linear-gradient(160deg,#8a8a8a 0%,#c9c9c9 40%,#6e6e6e 75%,#3a3a3a 100%)}
.eyebrow{color:var(--coral);font-size:14px;font-weight:600;letter-spacing:2px}
.about .eyebrow{position:absolute;left:669px;top:114px}
.about h2{position:absolute;left:669px;top:140px;color:var(--white);font-size:38px;font-weight:700;letter-spacing:5px}
.about p{position:absolute;left:669px;top:220px;width:440px;color:#e4e4e4;font-size:13.5px;line-height:31.4px}

/* levels */
.levels-title{position:absolute;left:0;top:1424px;width:1200px;text-align:center;font-size:36px;font-weight:700;letter-spacing:5px;line-height:37px}
.levels-title .accent{color:var(--coral)}
.levels-intro{position:absolute;left:196px;top:1560px;width:808px;text-align:center;font-size:13.5px;line-height:31px;color:#333}
.level{position:absolute;width:280px;text-align:center}
.level svg{display:block;margin:0 auto}
.level .num{font-size:26px;font-weight:700;margin-top:6px}
.level .label{font-size:13px;font-weight:500;letter-spacing:.3px;margin-top:6px}

/* video & stories */
.stories-band{position:absolute;left:0;top:2733px;width:1200px;height:803px;background:var(--dark)}
.video-frame{position:absolute;left:195px;top:2500px;width:809px;height:463px;background:var(--charcoal)}
.stories-title{position:absolute;left:0;top:3046px;width:1200px;text-align:center;color:var(--coral);font-size:36px;font-weight:700;letter-spacing:6px}
.quote{position:absolute;left:260px;top:3166px;width:680px;text-align:center;color:var(--white);font-size:23px;line-height:38px}
.quote-name{position:absolute;left:0;top:3316px;width:1200px;text-align:center;color:var(--coral);font-size:16px;font-weight:700}
.quote-date{position:absolute;left:0;top:3340px;width:1200px;text-align:center;color:var(--white);font-size:12px}
.dots{position:absolute;left:558px;top:3388px;display:flex;gap:22px}
.dots span{width:12px;height:12px;border-radius:50%;background:var(--white)}
.dots span:first-child{background:none;border:2px solid var(--white)}

/* contact */
.contact{position:absolute;left:0;top:3536px;width:1200px;height:586px;background:var(--coral);color:var(--white)}
.contact h2{position:absolute;left:196px;top:142px;font-size:36px;font-weight:700;letter-spacing:2px}
.contact .role{position:absolute;left:196px;top:204px;width:360px;font-size:13.5px;line-height:25px}
.contact address{position:absolute;left:196px;top:308px;font-style:normal;font-size:13.5px;line-height:19px;letter-spacing:.5px}
.contact address p{margin-bottom:10px}
.field-label{position:absolute;left:628px;font-size:13px}
.field{position:absolute;left:628px;width:376px;border:2px solid var(--white)}
.send{position:absolute;left:628px;top:470px;width:376px;height:38px;background:var(--white);color:var(--ink);font-size:16px;font-weight:600;letter-spacing:4px;display:flex;align-items:center;justify-content:center}

.site-footer{position:absolute;left:0;top:4122px;width:1200px;height:70px;background:var(--dark);color:var(--white);font-size:13px;display:flex;align-items:center;justify-content:center}
</style>
</head>
<body>

<header class="site-header">
  <div class="brand"><span class="brand-dot"></span><span class="brand-name">BRIGHT MEADOW</span></div>
  <div class="tagline">PREPARED TO PREVAIL</div>
  <div class="utility"><span>🛒 0</span><span class="login">LOG IN</span></div>
  <nav class="main-nav">
    <span class="active">HOME</span><span>ABOUT</span><span>HARBOR INSTITUTE</span><span>SHOP</span><span>LOST CERTIFICATE</span>
  </nav>
  <div class="nav-cta">JOIN HARBOR INSTITUTE</div>
</header>

<section class="hero">
  <div class="hero-media" role="img" aria-label="Video still of a bullet leaving a barrel with a bright muzzle flash"></div>
  <h1>Don't Settle For A<br>Gun Shop Class!</h1>
  <p class="lead">Your life may depend on what you learn in your concealed training</p>
  <div class="abs btn btn-solid" style="left:388px;top:346px;width:236px;height:42px">JOIN HARBOR INSTITUTE</div>
  <div class="abs btn btn-outline" style="left:388px;top:401px;width:236px;height:43px">GET TICKETS NOW</div>
  <div class="hero-divider"></div>
  <svg class="abs" style="left:721px;top:350px" width="72" height="72" viewBox="0 0 72 72">
    <circle cx="36" cy="36" r="30" fill="none" stroke="#f26267" stroke-width="2"/>
    <circle cx="36" cy="36" r="21" fill="#f26267"/>
    <path d="M36 2v10M36 60v10M2 36h10M60 36h10" stroke="#f26267" stroke-width="2"/>
    <path d="M31 27l14 9-14 9z" fill="#fff"/>
  </svg>
  <div class="play-film">PLAY FILM</div>
</section>

<section class="about">
  <div class="portrait" role="img" aria-label="Black and white portrait of instructor Dennis Pollock in a suit"></div>
  <div class="eyebrow">ABOUT THE INSTRUCTOR</div>
  <h2>DENNIS POLLOCK</h2>
  <p>Dennis Pollock is a true security expert with 25 years of experience in the security industry. He has appeared on KVN, WTR, ZBC &amp; MRN news outlets. He has been featured in numerous publications and has trained thousands to protect themselves and their homes from thugs and thieves. He is certified by both the NRL &amp; the NWDPA as a firearms instructor. He is also an NRL Range Safety Officer and Defensive Pistol Instructor.</p>
  <div class="abs btn btn-solid" style="left:669px;top:521px;width:171px;height:44px;gap:10px">READ MORE <svg width="20" height="20" viewBox="0 0 20 20"><circle cx="10" cy="10" r="7" fill="#fff"/><circle cx="10" cy="10" r="3" fill="#f26267"/></svg></div>
</section>

<h2 class="levels-title"><span class="accent">7 LEVELS</span> TRAINING<br>TAKING YOU<br><span class="accent">FROM ZERO TO HERO</span></h2>
<p class="levels-intro">Why do most people settle for a cheap &amp; quick concealed carry class? It's a fair question! Could you imagine a military soldier trained by a 2-hour class? How effective would they be in the heat of battle? If you want to be ready to SURVIVE an attack, YOU NEED MORE than a basic, run of the mill class! That's why we created a <b>PROPRIETARY 7 LEVEL TRAINING SYSTEM to take you all the way to the peak of readiness!</b></p>

<div class="level" style="left:173px;top:1730px">
  <svg width="130" height="90" viewBox="0 0 130 90"><path d="M10 8h110v24H60l-6 12H46l-4-6-12 48H8l14-56-12-2z" fill="#1d1d1d"/><rect x="20" y="2" width="20" height="8" fill="#1d1d1d"/></svg>
  <div class="num">01</div><div class="label">CONCEALED CARRY CLASS</div>
</div>
<div class="level" style="left:461px;top:1730px">
  <svg width="90" height="90" viewBox="0 0 90 90"><circle cx="45" cy="45" r="32" fill="none" stroke="#1d1d1d" stroke-width="7"/><circle cx="45" cy="45" r="14" fill="#f26267"/><path d="M45 6v18M45 66v18M6 45h18M66 45h18" stroke="#1d1d1d" stroke-width="6"/><path d="M4 16V4h12M74 4h12v12M4 74v12h12M86 74v12H74" fill="none" stroke="#1d1d1d" stroke-width="4"/></svg>
  <div class="num">02</div><div class="label">DYNAMIC DEFENSE SHOOTING</div>
</div>
<div class="level" style="left:749px;top:1730px">
  <svg width="90" height="90" viewBox="0 0 90 90"><rect x="12" y="52" width="16" height="30" fill="#1d1d1d"/><rect x="34" y="38" width="16" height="44" fill="#1d1d1d"/><path d="M56 30h16v36H56z" fill="#f26267"/><path d="M64 4l16 20H48z" fill="#f26267"/><rect x="56" y="70" width="16" height="4" fill="#1d1d1d"/><rect x="56" y="78" width="16" height="4" fill="#1d1d1d"/></svg>
  <div class="num">03</div><div class="label">FINE TUNING YOUR TECHNIQUE</div>
</div>

<div class="level" style="left:173px;top:1952px">
  <svg width="96" height="90" viewBox="0 0 96 90"><path d="M48 6L90 84H6z" fill="#f26267" stroke="#1d1d1d" stroke-width="6" stroke-linejoin="round"/><rect x="43" y="30" width="10" height="32" fill="#fff"/><rect x="43" y="67" width="10" height="9" fill="#fff"/></svg>
  <div class="num">04</div><div class="label">VIRTUAL THREAT-LAB</div>
</div>
<div class="level" style="left:461px;top:1952px">
  <svg width="96" height="90" viewBox="0 0 96 90"><rect x="42" y="22" width="12" height="44" rx="4" fill="#1d1d1d"/><rect x="38" y="28" width="20" height="20" rx="3" fill="#1d1d1d"/><circle cx="48" cy="16" r="6" fill="#1d1d1d"/><path d="M6 6l8 8M14 6l-8 8M82 74l8 8M90 74l-8 8M78 20l8 8M86 20l-8 8M14 62l8 8M22 62l-8 8" stroke="#1d1d1d" stroke-width="2.5"/><circle cx="12" cy="80" r="4" fill="#f26267"/><circle cx="86" cy="8" r="4" fill="#f26267"/><circle cx="70" cy="66" r="4" fill="#f26267"/><circle cx="26" cy="36" r="4" fill="#f26267"/><path d="M22 84q26 10 50-4" fill="none" stroke="#1d1d1d" stroke-width="2"/></svg>
  <div class="num">05</div><div class="label">TACTICAL SKILLS &amp; DRILLS</div>
</div>
<div class="level" style="left:749px;top:1952px">
  <svg width="90" height="90" viewBox="0 0 90 90"><path d="M45 4l36 12v26c0 22-16 38-36 46C25 80 9 64 9 42V16z" fill="#1d1d1d"/><path d="M28 44l12 12 24-24" fill="none" stroke="#f26267" stroke-width="9"/></svg>
  <div class="num">06</div><div class="label">CLOSE QUARTERS DEFENSE</div>
</div>

<div class="level" style="left:461px;top:2176px">
  <svg width="96" height="92" viewBox="0 0 96 92"><path d="M48 4c-16 0-26 12-26 24 0 16 26 40 26 40s26-24 26-40C74 16 64 4 48 4z" fill="none" stroke="#1d1d1d" stroke-width="6"/><circle cx="48" cy="28" r="10" fill="none" stroke="#f26267" stroke-width="5"/><path d="M20 60L4 88h88L76 60" fill="none" stroke="#1d1d1d" stroke-width="6" stroke-linejoin="round"/></svg>
  <div class="num">07</div><div class="label">LIVE SCENARIO THREAT-LAB</div>
</div>

<div class="abs btn btn-solid" style="left:461px;top:2398px;width:278px;height:44px;gap:12px">CLICK TO KNOW MORE <svg width="20" height="20" viewBox="0 0 20 20"><circle cx="10" cy="10" r="7" fill="#fff"/><circle cx="10" cy="10" r="3" fill="#f26267"/></svg></div>

<div class="stories-band"></div>
<div class="video-frame"></div>
<svg class="abs" style="left:563px;top:2695px" width="74" height="74" viewBox="0 0 74 74"><circle cx="37" cy="37" r="34" fill="none" stroke="#fff" stroke-width="3"/><path d="M29 22l24 15-24 15z" fill="#fff"/></svg>

<h2 class="stories-title">SUCCESS STORIES</h2>
<svg class="abs" style="left:124px;top:3185px" width="36" height="60" viewBox="0 0 36 60"><path d="M32 3L4 30l28 27" fill="none" stroke="#f26267" stroke-width="3"/></svg>
<svg class="abs" style="left:1040px;top:3185px" width="36" height="60" viewBox="0 0 36 60"><path d="M4 3l28 27L4 57" fill="none" stroke="#f26267" stroke-width="3"/></svg>
<p class="quote">I had never held a gun when I took the Bright Meadow Concealed Carry class and I'm hooked! I'm going all the way to level7! Thank you Bright Meadow Skills!</p>
<div class="quote-name">Marisa K.</div>
<div class="quote-date">October 14,2017</div>
<div class="dots"><span></span><span></span><span></span></div>

<section class="contact">
  <h2>DENNIS POLLOCK</h2>
  <p class="role">Nrl Firearms Instructor, Nwdpa Instructor &amp; Training Counsellor, News Correspondent, And Security Expert</p>
  <address>
    <p>P.O. BOX 4410<br>CEDAR HOLLOW, FL 32990</p>
    <p>BRIGHTMEADOWSKILLS@<br>MAILHAVEN.COM</p>
    <p>LOCAL: 555-014-7BMS (7267)<br>TOLL-FREE: 800-555-0199</p>
  </address>
  <span class="field-label" style="top:74px">Name*</span>
  <div class="field" style="top:99px;height:35px"></div>
  <span class="field-label" style="top:152px">Email*</span>
  <div class="field" style="top:177px;height:35px"></div>
  <span class="field-label" style="top:229px">Phone</span>
  <div class="field" style="top:254px;height:34px"></div>
  <span class="field-label" style="top:306px">Message</span>
  <div class="field" style="top:330px;height:121px"></div>
  <div class="send">SEND</div>
</section>

<footer class="site-footer">Copyright Bright Meadow Skills 2021 - All Rights Reserved</footer>

</body>
</html>
```